Business Cards

Need business card design that I can update for new employees and details. Needs to incorporate our logo, be bright and fun (in line with tourism and holidays)
Would like a Map of Western Australia on the front with locations all the caravan parks we own (just purchased Tom Price so please include that as well as others listed on our website).
Target Market(s)
Famillies
Contact Information for Business Card
5 Cards -
Neil Perrow (Director) e: perrow@wattlebay.com.au p: 0491 570 156
Mira Perrow (Director) e: perrow@wattlebay.com.au p: 0491 570 157
Owen Halvey (General Manager) e: halvey@wattlebay.com.au p: 0491 570 158
Helen Halvey (General Manager) e: halvey@wattlebay.com.au p: 0491 570 159
Colin Danby (Training and Operations Manager) - e: danby@wattlebay.com.au p:0491 570 110
Colors
Look and feel

```html
<!DOCTYPE html>
<html lang="en">
<head>
<meta charset="utf-8">
<title>Wattle Bay Tourist Parks – Business Card</title>
<link href="https://fonts.googleapis.com/css2?family=Crimson+Pro:wght@400&family=PT+Sans:wght@400&display=swap" rel="stylesheet">
<style>
  :root {
    --teal: #3fc0cc;
    --ink: #4a4a4c;
    --ink-dark: #2b2b2b;
    --card: #f8f9f9;
    --page: #e4e6e7;
    --white: #ffffff;
  }
  * { margin: 0; padding: 0; box-sizing: border-box; }
  html, body {
    width: 1200px;
    height: 900px;
    overflow: hidden;
    background: var(--page);
  }
  .card {
    position: absolute;
    left: 120px;
    top: 152px;
    width: 960px;
    height: 595px;
    background: var(--card);
    overflow: hidden;
    box-shadow: 0 6px 24px rgba(0,0,0,0.12);
  }
  .card__band {
    position: absolute;
    inset: 0;
    width: 960px;
    height: 595px;
  }
  .brand {
    position: absolute;
    left: 40px;
    top: 85px;
    width: 480px;
    text-align: center;
    font-family: "Crimson Pro", Georgia, serif;
    font-weight: 400;
    color: var(--ink);
  }
  .brand__mark {
    display: block;
    width: 138px;
    height: 138px;
    margin: 0 auto 12px;
    background: var(--teal);
  }
  .brand__name {
    display: block;
    font-size: 52px;
    line-height: 1;
    letter-spacing: 0.1em;
    text-transform: uppercase;
  }
  .brand__tagline {
    display: block;
    margin-top: 10px;
    font-size: 23px;
    line-height: 1;
    letter-spacing: 0.22em;
    text-transform: uppercase;
  }
  .person {
    position: absolute;
    left: 62px;
    top: 345px;
  }
  .person__name {
    font-family: "Crimson Pro", Georgia, serif;
    font-weight: 400;
    font-size: 40px;
    line-height: 1.1;
    letter-spacing: 0.02em;
    text-transform: uppercase;
    color: var(--teal);
  }
  .person__role {
    margin-top: 4px;
    font-family: "PT Sans", Arial, sans-serif;
    font-size: 24px;
    color: var(--ink-dark);
  }
  .contact {
    position: absolute;
    left: 62px;
    top: 512px;
    display: flex;
    gap: 48px;
    font-family: "PT Sans", Arial, sans-serif;
    font-size: 29px;
    color: var(--white);
  }
  .contact__item {
    display: flex;
    align-items: center;
    gap: 14px;
  }
  .contact__icon {
    width: 36px;
    height: 36px;
    background: var(--white);
    display: flex;
    align-items: center;
    justify-content: center;
  }
</style>
</head>
<body>
  <div class="card">
    <svg class="card__band" viewBox="0 0 960 595" aria-hidden="true">
      <path d="M0 459 L480 459 C580 459 630 420 700 372 C780 318 870 278 960 258 L960 595 L0 595 Z" fill="var(--teal)"/>
    </svg>

    <div class="brand">
      <span class="brand__mark" aria-hidden="true"></span>
      <span class="brand__name">Wattle Bay</span>
      <span class="brand__tagline">Tourist Parks</span>
    </div>

    <div class="person">
      <p class="person__name">Neil Perrow</p>
      <p class="person__role">Director</p>
    </div>

    <div class="contact">
      <div class="contact__item">
        <span class="contact__icon">
          <svg width="26" height="26" viewBox="0 0 24 24" aria-hidden="true">
            <path fill="var(--teal)" d="M6.6 10.8c1.4 2.8 3.8 5.1 6.6 6.6l2.2-2.2c.3-.3.7-.4 1-.2 1.1.4 2.3.6 3.6.6.6 0 1 .4 1 1V20c0 .6-.4 1-1 1C10.6 21 3 13.4 3 4c0-.6.4-1 1-1h3.5c.6 0 1 .4 1 1 0 1.3.2 2.5.6 3.6.1.3 0 .7-.2 1l-2.3 2.2z"/>
          </svg>
        </span>
        <span>0491 570 156</span>
      </div>
      <div class="contact__item">
        <span class="contact__icon">
          <svg width="26" height="26" viewBox="0 0 24 24" aria-hidden="true">
            <rect x="2.5" y="5.5" width="19" height="13" fill="none" stroke="var(--teal)" stroke-width="1.8"/>
            <path d="M2.5 5.5 L12 13 L21.5 5.5" fill="none" stroke="var(--teal)" stroke-width="1.8"/>
          </svg>
        </span>
        <span>perrow@wattlebay.com.au</span>
      </div>
    </div>
  </div>
</body>
</html>
```